Family business needs stationery redesign with new logo

Family owned company, established in 1987 wanting a brand 'refresh'. We are an electrical, refrigeration and construction company based in the Barkly Region Northern Territory, Australia. We have a new logo we would like to use which is uploaded along with our current letterhead and email signature. We are also dropping the word 'contractors' so please do not include this on any designs. Please note also, the 'orange' color used in our logo and designs should be Northern Territory red ochre which is as follows:

RGB (Hex): #C75B12
PantoneĀ® 159 C
CMYK: 1 / 74 / 100 / 7

We are needing our stationery redesigned using our new logo. Please include letterheads, business cards, envelopes, and email signatures.

We currently use our business letterheads for quotations, invoices, letters, HR matters, and internal memos.

We also need a separate simplified letterhead for internal paperwork such as employee leave forms, meeting agendas, and meeting minutes etc.

Reason: Needing more submissions of full package designs. We are wanting all our stationery, including business cards, letterheads, email signatures, envelopes, etc to be cohesive. We also require ALL the information, as supplied on our template letterhead, to be included on the new letterhead designs. including electrical license no.etc Thank you, R&W

Reason: needing more time as work has got in the way of looking over designs. A lot of designs not meeting the brief/criteria.

Industry/Entity Type

Business

Colors
0355a3
f37122

Requirements
Must have
• The 'orange' color used in the designs should be Northern Territory red ochre which is as follows:
• RGB (Hex): #C75B12
• PantoneĀ® 159 C
• CMYK: 1 / 74 / 100 / 7
• ***MUST INCLUDE ALL INFORMATION THAT IS ON OUR CURRENT LETTERHEAD***
Should not have
• Please do not include the word 'contractors'

```html
<!DOCTYPE html>
<html lang="en">
<head>
<meta charset="utf-8">
<title>R&amp;W Stationery Suite</title>
<link href="https://fonts.googleapis.com/css2?family=Tinos&family=Arimo:wght@400;700&family=Michroma&display=swap" rel="stylesheet">
<style>
:root{
  --navy:#1b2f6b;
  --ochre:#c75b12;
  --paper:#ffffff;
  --ground:#ececec;
  --ink:#333a48;
}
*{box-sizing:border-box;margin:0;padding:0}
html,body{width:1200px;height:938px;overflow:hidden;background:var(--ground)}
.canvas{position:relative;width:1200px;height:938px;background:var(--ground)}
.sheet{position:absolute;background:var(--paper);overflow:hidden}
.wave{position:absolute;left:0;bottom:0;width:100%;display:block}
.brand{font-family:"Tinos",serif;color:var(--navy);font-weight:400;line-height:1}
.tagline{font-family:"Tinos",serif;color:var(--navy);line-height:1.05}

/* letterhead */
.letterhead{left:184px;top:68px;width:386px;height:544px}
.letterhead .brand{position:absolute;left:18px;top:28px;font-size:30px}
.letterhead .tagline{position:absolute;left:105px;top:29px;font-size:9.4px}
.contact{position:absolute;right:18px;top:24px;text-align:right;font-family:"Tinos",serif;font-size:5.4px;line-height:1.25;color:var(--ink)}
.contact .gap{height:3px}
.contact i{display:inline-block;width:5px;height:5px;border-radius:50%;background:var(--navy);margin-left:3px;vertical-align:middle}
.letter{position:absolute;left:37px;top:138px;width:295px;font-family:"Arimo",sans-serif;font-size:5.4px;line-height:1.55;color:var(--ink)}
.letter p{margin-bottom:8px}
.letter .spaced{margin-bottom:26px}
.letter strong{font-weight:700}
.signature{width:40px;height:22px;background:linear-gradient(90deg,#e9e9ec,#d6d7dc);margin:6px 0 8px}
.letterhead .wave{height:84px}

/* folder */
.folder{left:636px;top:42px;width:458px;height:574px}
.folder .lockup{position:absolute;left:0;right:0;top:240px;text-align:center}
.folder .brand{font-size:46px}
.folder .tagline{margin-top:14px;font-size:16.5px;line-height:1.12}
.folder .wave{height:98px}

/* business cards */
.card{width:176px;height:100px;border-radius:7px}
.card-front{left:46px;top:659px}
.card-front .brand{position:absolute;left:80px;top:21px;font-size:15px}
.card-front .tagline{position:absolute;right:10px;top:22px;font-size:5.2px;text-align:right}
.card-front .wave{height:100px}
.card-front .person{position:absolute;left:100px;top:60px;width:60px;text-align:center;font-family:"Tinos",serif;color:var(--navy);font-size:7.4px;line-height:1}
.card-front .person span{display:block;font-size:6px;margin-top:1px}
.card-front .details{position:absolute;left:7px;top:63px;font-family:"Tinos",serif;color:#fff;font-size:3.6px;line-height:1.25}
.card-back{left:46px;top:786px;height:99px}
.card-back .brand{position:absolute;left:44px;top:42px;font-size:16px}
.card-back .tagline{position:absolute;left:95px;top:41px;font-size:5.2px}

/* envelope front */
.envelope{left:266px;top:673px;width:432px;height:208px}
.envelope .brand{position:absolute;left:16px;top:26px;font-size:27px}
.envelope .tagline{position:absolute;left:101px;top:27px;font-size:8.6px}
.envelope .wave{height:93px}

/* envelope back */
.envelope-back{left:737px;top:673px;width:432px;height:207px}
.flap{position:absolute;left:0;top:0;width:100%;height:72px;background:var(--navy);border-radius:0 0 38px 38px;display:flex;align-items:center;justify-content:center}
.flap span{font-family:"Michroma",sans-serif;color:#fff;font-size:10.5px;letter-spacing:2.6px;margin-top:-8px}
</style>
</head>
<body>
<div class="canvas">

  <!-- Letterhead -->
  <section class="sheet letterhead">
    <div class="brand">R&amp;W</div>
    <div class="tagline">Electrical<br>Refrigeration<br>Building Services</div>
    <div class="contact">
      Unit 4, 12 Ochre St,<i></i><br>Tennant Creek NT
      <div class="gap"></div>
      08 8962 1104<i></i><br>0412 558 903<i></i><br>08 8962 1180<i></i>
      <div class="gap"></div>
      office@rwservices.com.au<i></i><br>www.rwservices.com.au<i></i>
    </div>
    <div class="letter">
      <p>July 2, 2012</p>
      <p><strong>Dear Sam,</strong><br>Harbour House, Stuart St, Australia</p>
      <p class="spaced">is simply dummy text of the printing and typesetting industry. Lorem Ipsum has been the industry's standard dummy text ever since the 1500s, when an unknown printer took a galley of type and scrambled it to make a type specimen book. It has survived not only five centuries, but also the leap into electronic typesetting, remaining essentially unchanged. It was popularised in the 1960s with the release of Letraset sheets containing Lorem Ipsum passages, and more recently with desktop publishing software like Aldus PageMaker including versions of Lorem Ipsum.</p>
      <p class="spaced">is simply dummy text of the printing and typesetting industry. Lorem Ipsum has been the industry's standard dummy text ever since the 1500s, when an unknown printer took a galley of type and scrambled it to make</p>
      <p>is simply dummy text of the printing and typesetting industry. Lorem Ipsum has been the industry's standard dummy text ever since the 1500s, when an unknown printer took a galley of type and scrambled it to make a type specimen book. It has survived not only five centuries, but also the leap into electronic typesetting, remaining essentially unchanged. It was popularised in the 1960s with the release of Letraset sheets containing Lorem Ipsum passages, and more recently with desktop publishing software like Aldus PageMaker including versions of Lorem Ipsum.</p>
      <p>Best Regards,</p>
      <div class="signature" role="img" aria-label="Handwritten signature"></div>
      <p><strong>Lewis Crane</strong><br>Director</p>
      <p>Harbour House, Stuart St, Australia</p>
    </div>
    <svg class="wave" viewBox="0 0 100 22" preserveAspectRatio="none" aria-hidden="true">
      <path d="M0 3.6 C28 3.6 44 20 72 20.6 C84 20.9 93 18.6 100 14.8 L100 22 L0 22 Z" fill="var(--navy)"/>
      <path d="M0 0 C28 0 44 15.6 72 17.6 C84 18.4 93 15.6 100 11.6 L100 14.2 C92 18.4 82 20.4 70 19.8 C44 18.6 28 1.8 0 1.8 Z" fill="var(--ochre)"/>
    </svg>
  </section>

  <!-- Presentation folder -->
  <section class="sheet folder">
    <div class="lockup">
      <div class="brand">R&amp;W</div>
      <div class="tagline">Electrical<br>Refrigeration<br>Building Services</div>
    </div>
    <svg class="wave" viewBox="0 0 100 22" preserveAspectRatio="none" aria-hidden="true">
      <path d="M0 3.6 C28 3.6 44 20 72 20.6 C84 20.9 93 18.6 100 14.8 L100 22 L0 22 Z" fill="var(--navy)"/>
      <path d="M0 0 C28 0 44 15.6 72 17.6 C84 18.4 93 15.6 100 11.6 L100 14.2 C92 18.4 82 20.4 70 19.8 C44 18.6 28 1.8 0 1.8 Z" fill="var(--ochre)"/>
    </svg>
  </section>

  <!-- Business card front -->
  <section class="sheet card card-front">
    <svg class="wave" viewBox="0 0 176 100" preserveAspectRatio="none" aria-hidden="true">
      <path d="M0 34 C48 34 78 88 138 90 C154 90.5 167 86 176 79 L176 100 L0 100 Z" fill="var(--navy)"/>
      <path d="M0 29 C48 30 78 80 136 84.5 C154 86 167 80 176 71 L176 75.5 C167 85 152 90 134 88.5 C78 85 48 33 0 32 Z" fill="var(--ochre)"/>
    </svg>
    <div class="brand">R&amp;W</div>
    <div class="tagline">Electrical<br>Refrigeration<br>Building Services</div>
    <div class="person">Dana Hollis<span>Owner / C.E.O</span></div>
    <div class="details">
      Unit 4, 12 Ochre St,<br>Tennant Creek NT<br>08 8962 1104<br>0412 558 903<br>08 8962 1180<br>office@rwservices.com.au<br>www.rwservices.com.au
    </div>
  </section>

  <!-- Business card back -->
  <section class="sheet card card-back">
    <div class="brand">R&amp;W</div>
    <div class="tagline">Electrical<br>Refrigeration<br>Building Services</div>
  </section>

  <!-- Envelope front -->
  <section class="sheet envelope">
    <div class="brand">R&amp;W</div>
    <div class="tagline">Electrical<br>Refrigeration<br>Building Services</div>
    <svg class="wave" viewBox="0 0 100 21.5" preserveAspectRatio="none" aria-hidden="true">
      <path d="M0 1.8 C28 1.8 44 19.6 72 20.2 C84 20.5 93 18.2 100 14.2 L100 21.5 L0 21.5 Z" fill="var(--navy)"/>
      <path d="M0 0 C28 0 44 14.4 72 16.6 C84 17.4 93 14.6 100 10.6 L100 13.4 C92 17.6 82 19.6 70 19 C44 17.6 28 1.2 0 1.2 Z" fill="var(--ochre)"/>
    </svg>
  </section>

  <!-- Envelope back -->
  <section class="sheet envelope-back">
    <div class="flap"><span>www.rwservices.com.au</span></div>
  </section>

</div>
</body>
</html>
```